Moravel Aesthetic Doctor

I require an elegant, luxurious looking business card for my aesthetic business. I am a doctor and that will set me aside from competitors. I am planning to provide home and spa based treatments to clients with high expectations. I have attached my logo.

```html
<!DOCTYPE html>
<html lang="en">
<head>
<meta charset="utf-8">
<title>Moravel Aesthetic Doctor – Business Card</title>
<link href="https://fonts.googleapis.com/css2?family=Marcellus&family=Roboto:wght@300;400&display=swap" rel="stylesheet">
<style>
  :root {
    --backdrop: #3b3b3c;
    --card: #1d1d1f;
    --silver: #b9bcc0;
    --silver-dim: #7d8085;
    --blue: #3ba3e3;
    --blue-deep: #0f6fb8;
    --blue-light: #8cc9f0;
    --text: #e6e6e6;
  }
  * { margin: 0; padding: 0; box-sizing: border-box; }
  html, body { width: 799px; height: 1200px; overflow: hidden; background: var(--backdrop); }
  .canvas {
    width: 799px; height: 1200px; position: relative;
    display: flex; flex-direction: column; align-items: center; justify-content: space-around;
    padding: 60px 0;
  }
  .card {
    width: 620px; height: 356px; background: var(--card);
    border-radius: 6px; position: relative; overflow: hidden;
    box-shadow: 0 14px 30px rgba(0,0,0,.45);
  }
  /* Front */
  .card--front { display: flex; align-items: center; justify-content: center; gap: 16px; }
  .front-mark { width: 22px; height: 22px; border-radius: 50%; border: 2px solid var(--silver-dim); }
  .front-name {
    font-family: "Roboto", sans-serif; font-weight: 300; font-size: 40px;
    letter-spacing: 4px; color: var(--silver);
  }
  /* Back */
  .brand { position: absolute; left: 30px; top: 34px; }
  .brand__name {
    font-family: "Marcellus", serif; font-size: 52px; line-height: 1;
    color: var(--silver); letter-spacing: 2px; text-transform: uppercase;
  }
  .brand__role {
    font-family: "Marcellus", serif; font-size: 19px; color: var(--blue);
    letter-spacing: 3px; text-transform: uppercase; margin-top: 2px;
  }
  .doctor { position: absolute; left: 30px; top: 142px; font-family: "Roboto", sans-serif; }
  .doctor__name { font-weight: 300; font-size: 24px; color: var(--text); }
  .doctor__post { font-size: 11px; margin-left: 4px; }
  .doctor__qual { font-size: 14px; color: var(--blue); line-height: 1.25; margin-top: 4px; }
  .contacts {
    position: absolute; left: 30px; top: 236px; list-style: none;
    font-family: "Roboto", sans-serif; font-size: 15px; color: var(--text);
  }
  .contacts li { display: flex; align-items: center; gap: 10px; height: 24px; white-space: nowrap; }
  .contacts svg { width: 13px; height: 13px; fill: var(--blue); flex: none; }
  .contacts .sep { margin: 0 6px; }
  .contacts .social { color: var(--text); font-weight: 400; }
  .portrait-art {
    position: absolute; right: 0; top: 80px; width: 240px; height: 276px;
    background: linear-gradient(160deg, var(--blue-light) 0%, var(--blue) 45%, var(--blue-deep) 100%);
    border-top-left-radius: 120px 130px;
    opacity: .92;
  }
</style>
</head>
<body>
<main class="canvas">
  <section class="card card--front" aria-label="Card front">
    <span class="front-mark"></span>
    <span class="front-name">Moravel</span>
  </section>

  <section class="card card--back" aria-label="Card back">
    <div class="brand">
      <div class="brand__name">Moravel</div>
      <div class="brand__role">Aesthetic Doctor</div>
    </div>
    <div class="doctor">
      <div class="doctor__name">Dr Elin Varga<span class="doctor__post">MRCPCH MD</span></div>
      <div class="doctor__qual">Australasian Diploma of<br>Aesthetic Medicine</div>
    </div>
    <ul class="contacts">
      <li>
        <svg viewBox="0 0 24 24"><path d="M6.6 10.8a15.1 15.1 0 0 0 6.6 6.6l2.2-2.2a1 1 0 0 1 1-.25 11.4 11.4 0 0 0 3.6.57 1 1 0 0 1 1 1V20a1 1 0 0 1-1 1A17 17 0 0 1 3 4a1 1 0 0 1 1-1h3.5a1 1 0 0 1 1 1c0 1.25.2 2.450.57 3.57a1 1 0 0 1-.25 1z"/></svg>
        <span>0800 555 014</span>
      </li>
      <li>
        <svg viewBox="0 0 24 24"><path d="M2 5h20v14H2z M2 5l10 8 10-8" fill="none" stroke="#3ba3e3" stroke-width="2"/></svg>
        <span>elin@moravel.co.nz</span>
      </li>
      <li>
        <svg viewBox="0 0 24 24"><circle cx="12" cy="12" r="10" fill="none" stroke="#3ba3e3" stroke-width="2"/><path d="M2 12h20M12 2c3 3 3 17 0 20M12 2c-3 3-3 17 0 20" fill="none" stroke="#3ba3e3" stroke-width="1.6"/></svg>
        <span>www.moravel.co.nz<span class="sep">|</span>Follow us on: <span class="social">@moravel</span></span>
      </li>
    </ul>
    <div class="portrait-art" role="img" aria-label="Flowing blue stylised portrait artwork"></div>
  </section>
</main>
</body>
</html>
```